Business Card for Financial Asset Management Company

Now we are launching a new company based in Tokyo.
The company information is below;

Company Name: Velmora Advisory

Operations: Financial assets management, Proposing forming portfolio of assets, Consulting service, and advising to enhance your company's financial health

Corporate Colour: Japan Blue or Navy like below
http://stuweb.ax.tolvaric.edu/kpimra/pics/Shade/Mist-Shade-217.jpg

It's dark and deep, and will get to fit to our clients as our relationships last longer and longer.

Our images for this colour are "Japanese style" and "pride in our craftmanship" , and also "gentle".

Corporate Key Image: an order taker who is sincere, polite, but courageous

We don't have our logo yet so please feel free to put any symbol on your design.

Please do not hesitate about asking any questions.
Thank you :-)

Reason: We are still discussin on final decision. Thank you for your understanding.

```html
<!DOCTYPE html>
<html lang="en">
<head>
<meta charset="utf-8">
<title>Velmora Advisory — Business Card</title>
<link rel="stylesheet" href="https://fonts.googleapis.com/css2?family=Open+Sans:wght@300;400;600&display=swap">
<style>
  :root {
    --navy-deep: #172a78;
    --navy-mid: #1d3a8e;
    --navy-glow: #22449c;
    --wave: #2a5cb0;
    --ink-white: #ffffff;
    --ink-soft: #e8edf8;
  }
  html, body {
    margin: 0;
    padding: 0;
    width: 1200px;
    height: 726px;
    overflow: hidden;
    background: var(--navy-deep);
  }
  .card {
    position: relative;
    width: 1200px;
    height: 726px;
    overflow: hidden;
    background: radial-gradient(ellipse 60% 70% at 50% 45%, var(--navy-glow) 0%, var(--navy-mid) 45%, var(--navy-deep) 100%);
    font-family: "Open Sans", Arial, sans-serif;
    color: var(--ink-white);
  }
  .card__waves {
    position: absolute;
    inset: 0;
    width: 1200px;
    height: 726px;
  }
  .brand {
    position: absolute;
    left: 0;
    right: 0;
    top: 140px;
    display: flex;
    flex-direction: column;
    align-items: center;
  }
  .brand__dot {
    width: 120px;
    height: 120px;
    border-radius: 50%;
    background: var(--ink-white);
    margin-bottom: 22px;
  }
  .brand__name {
    margin: 0;
    font-weight: 600;
    font-size: 60px;
    line-height: 60px;
    letter-spacing: 0.5px;
    text-align: center;
    color: var(--ink-white);
  }
  .services {
    position: absolute;
    left: 0;
    right: 0;
    top: 510px;
    margin: 0;
    text-align: center;
    font-weight: 400;
    font-size: 31px;
    color: var(--ink-white);
  }
  .divider {
    position: absolute;
    left: 407px;
    top: 574px;
    width: 384px;
    height: 2px;
    background: var(--ink-white);
  }
  .website {
    position: absolute;
    left: 0;
    right: 0;
    top: 598px;
    margin: 0;
    text-align: center;
    font-weight: 300;
    font-size: 24px;
    color: var(--ink-soft);
  }
</style>
</head>
<body>
  <main class="card">
    <svg class="card__waves" viewBox="0 0 1200 726" aria-hidden="true">
      <g fill="var(--wave)" fill-opacity="0.13">
        <circle cx="-20" cy="900" r="500"/>
        <circle cx="1220" cy="900" r="500"/>
        <circle cx="600" cy="980" r="520"/>
        <circle cx="250" cy="960" r="400"/>
        <circle cx="950" cy="960" r="400"/>
      </g>
    </svg>

    <header class="brand">
      <div class="brand__dot"></div>
      <h1 class="brand__name">Velmora<br>Advisory</h1>
    </header>

    <p class="services">Financial Assets . Proposing Porfolio . Consulting Services</p>
    <div class="divider"></div>
    <p class="website">www.velmoraadvisory.jp</p>
  </main>
</body>
</html>
```